Brellwick Partners, LLC Stationary

Brellwick Partners, LLC is a new financial planning and consulting company. We are looking for designs on business cards, letterhead, envelopes, and anything else that would be useful. Our preference for business card design is two sided. We are looking for a professional and clean look with incorporating the logo and patriotic feel. Thank you to all who participate and good luck!

```html
<!DOCTYPE html>
<html lang="en">
<head>
<meta charset="utf-8">
<title>Brellwick Partners, LLC – Business Card</title>
<link href="https://fonts.googleapis.com/css2?family=Arimo:wght@400;700&display=swap" rel="stylesheet">
<style>
  :root {
    --page-bg: #e9e6e1;
    --brand-red: #c4202b;
    --brand-red-dark: #8e1820;
    --brand-navy: #163e6b;
    --brand-navy-light: #2f5f91;
    --card-white: #ffffff;
    --card-grey: #eeeeef;
    --text-grey: #555a60;
    --rule-grey: #b9bcc0;
  }
  * { box-sizing: border-box; margin: 0; padding: 0; }
  html, body {
    width: 1200px; height: 950px; overflow: hidden;
    background: var(--page-bg);
    font-family: "Arimo", Arial, sans-serif;
  }
  .canvas { position: relative; width: 1200px; height: 950px; }

  .card {
    position: absolute; width: 700px; height: 400px;
    border-radius: 4px; overflow: hidden;
    box-shadow: 0 14px 30px rgba(0,0,0,.25);
  }

  /* Back side */
  .card-back {
    left: 110px; top: 50px;
    background: linear-gradient(110deg, var(--brand-red) 0%, #b01d27 60%, var(--brand-red-dark) 100%);
    display: flex; flex-direction: column; align-items: center; justify-content: center;
    color: var(--card-white);
  }
  .back-name { font-size: 44px; font-weight: 700; letter-spacing: 1px; }
  .back-web { margin-top: 26px; font-size: 18px; letter-spacing: 2px; }

  /* Front side */
  .card-front {
    left: 390px; top: 500px;
    background: linear-gradient(90deg, var(--card-white) 0%, var(--card-white) 45%, var(--card-grey) 100%);
  }
  .front-band {
    position: absolute; left: 0; right: 0; top: 62px; height: 92px;
    background: linear-gradient(90deg, var(--brand-navy) 0%, var(--brand-navy) 55%, var(--brand-navy-light) 80%, var(--brand-navy) 100%);
    border-top: 4px solid var(--card-white);
    border-bottom: 4px solid var(--card-white);
    outline: 3px solid var(--brand-red);
    color: var(--card-white);
    display: flex; flex-direction: column; justify-content: center;
    padding-left: 330px;
  }
  .person-name { font-size: 26px; font-weight: 700; letter-spacing: 1px; }
  .person-title { font-size: 17px; margin-top: 4px; letter-spacing: 1px; }

  .front-logo {
    position: absolute; left: 30px; top: 250px; width: 300px;
    display: flex; align-items: center; gap: 10px;
    white-space: nowrap;
  }
  .logo-dot { width: 18px; height: 18px; border-radius: 50%; background: var(--brand-navy); flex: none; }
  .logo-name { font-size: 20px; font-weight: 700; color: var(--brand-navy); }

  .front-divider {
    position: absolute; left: 350px; top: 192px; width: 1px; height: 180px;
    background: var(--rule-grey);
  }
  .contact {
    position: absolute; left: 372px; top: 196px;
    list-style: none; color: var(--text-grey); font-size: 19px; line-height: 26px;
  }
  .contact li { display: flex; align-items: center; gap: 8px; white-space: nowrap; }
  .contact svg { width: 16px; height: 16px; fill: var(--brand-navy); flex: none; }
</style>
</head>
<body>
<main class="canvas">
  <section class="card card-back" aria-label="Business card, back side">
    <div class="back-name">Brellwick Partners, LLC</div>
    <div class="back-web">www.brellwick.com</div>
  </section>

  <section class="card card-front" aria-label="Business card, front side">
    <div class="front-band">
      <div class="person-name">DANIEL MARSH</div>
      <div class="person-title">PRESIDENT</div>
    </div>

    <div class="front-logo">
      <span class="logo-dot"></span>
      <span class="logo-name">Brellwick Partners, LLC</span>
    </div>

    <div class="front-divider"></div>

    <ul class="contact">
      <li class="address">2710 Carrow Lane</li>
      <li class="address">Elmstead, NY 11420</li>
      <li>
        <svg viewBox="0 0 16 16" aria-hidden="true"><path d="M3 1h3l1 4-2 1a9 9 0 0 0 5 5l1-2 4 1v3c0 1-1 2-2 2A13 13 0 0 1 1 3c0-1 1-2 2-2z"/></svg>
        555 8470 2216
      </li>
      <li>
        <svg viewBox="0 0 16 16" aria-hidden="true"><rect x="4" y="1" width="8" height="4"/><rect x="1" y="6" width="14" height="6" rx="1"/><rect x="4" y="10" width="8" height="5"/></svg>
        555 4629 3184
      </li>
      <li>
        <svg viewBox="0 0 16 16" aria-hidden="true"><path d="M1 3h14v10H1z M1 3l7 6 7-6" stroke="#fff" stroke-width="1"/></svg>
        daniel@brellwick.com
      </li>
      <li>
        <svg viewBox="0 0 16 16" aria-hidden="true"><circle cx="8" cy="8" r="7"/></svg>
        www.brellwick.com
      </li>
    </ul>
  </section>
</main>
</body>
</html>
```